Healthcare and Professional IT Services Company need a redesigned business card

We are a IT Services company that targets small medical practices and professional business such as Attorneys, Accounts, Architects etc. We want to communicate a professional yet friendly image using recent logo redesign here on ArtHarbor. Like to see the colors blue and orange in the design. Must use the Tall Pine Computing as displayed in the new logo - then also want to incorporate the fish logo as well.

Target Market(s)

Small medical and professional services

Industry/Entity Type

It Company

Contact Information for Business Card

The usual stuff, place for name address phone website. Also maybe our tagline which is "rooted in technology"

Requirements
Must have
• My new logo and the fish somewhere on the card

```html
<!DOCTYPE html>
<html lang="en">
<head>
<meta charset="utf-8">
<title>Tall Pine Computing – Business Card</title>
<link rel="stylesheet" href="https://fonts.googleapis.com/css2?family=Quicksand:wght@600&family=Tinos&family=Open+Sans:wght@400&display=swap">
<style>
  :root {
    --bg: #e9e6e1;
    --card-white: #ffffff;
    --card-black: #0b0b0c;
    --brand-blue: #2aa3dd;
    --brand-blue-deep: #1b84c2;
    --brand-orange: #f2a33a;
    --ink: #111111;
    --band-black: #0d0d0d;
  }
  * { box-sizing: border-box; margin: 0; padding: 0; }
  html, body { width: 1200px; height: 892px; overflow: hidden; }
  body {
    background: var(--bg);
    display: flex;
    flex-direction: column;
    align-items: center;
    justify-content: center;
    gap: 40px;
  }
  .card {
    position: relative;
    width: 600px;
    height: 343px;
    overflow: hidden;
    box-shadow: 0 6px 18px rgba(0,0,0,.18);
  }

  /* Front */
  .card--front { background: var(--card-white); }
  .front__mascot {
    position: absolute; left: 150px; top: 34px;
    width: 130px; height: 100px;
    border-radius: 50% 40% 45% 50%;
    background: radial-gradient(circle at 50% 45%, #d8effa 0%, #9fd5f0 70%, #7cc4ea 100%);
  }
  .brand {
    position: absolute;
    display: flex; align-items: center; gap: 10px;
    font-family: "Quicksand", sans-serif;
    font-weight: 600;
    color: var(--brand-blue);
    line-height: 1;
    white-space: nowrap;
  }
  .brand__mark { width: 12px; height: 12px; background: var(--brand-orange); flex: none; }
  .front__brand { left: 40px; top: 156px; font-size: 26px; }
  .front__divider {
    position: absolute; left: 336px; top: 40px;
    width: 2px; height: 200px; background: var(--ink);
  }
  .contact { position: absolute; left: 356px; top: 52px; }
  .contact__name {
    font-family: "Tinos", serif;
    font-size: 36px; color: var(--ink);
    margin-bottom: 22px; margin-left: 10px;
  }
  .contact__list { list-style: none; font-family: "Open Sans", sans-serif; font-size: 14px; color: var(--ink); }
  .contact__item { display: flex; align-items: flex-start; gap: 8px; margin-bottom: 6px; line-height: 1.35; }
  .contact__icon { flex: none; width: 15px; height: 15px; margin-top: 2px; }
  .band { position: absolute; left: 0; right: 0; bottom: 0; height: 76px; }
  .band__stripe { height: 10px; background: var(--brand-blue-deep); }
  .band__stripe--bottom { height: 12px; }
  .band__body {
    height: 54px; background: var(--band-black);
    display: flex; align-items: center; justify-content: center;
    font-family: "Tinos", serif; font-size: 19px; color: #ffffff;
  }

  /* Back */
  .card--back { background: var(--card-black); }
  .back__mascot {
    position: absolute; left: 205px; top: 40px;
    width: 190px; height: 150px;
    border-radius: 50% 42% 46% 50%;
    background: radial-gradient(circle at 50% 45%, #123a52 0%, #1b6a99 65%, #2aa3dd 100%);
  }
  .back__brand { left: 0; right: 0; top: 222px; justify-content: center; font-size: 40px; }
</style>
</head>
<body>

  <section class="card card--front" aria-label="Business card front">
    <div class="front__mascot" role="img" aria-label="Cartoon fish mascot illustration in blue outline"></div>
    <div class="brand front__brand"><span class="brand__mark"></span><span>Tall Pine Computing</span></div>
    <div class="front__divider"></div>

    <div class="contact">
      <p class="contact__name">Dana Reyes</p>
      <ul class="contact__list">
        <li class="contact__item">
          <svg class="contact__icon" viewBox="0 0 16 16"><rect width="16" height="16" rx="2" fill="#111"/><path d="M5 3.5c.6 0 1 1.6 1 2.2 0 .6-.8.8-.6 1.4.4 1.2 1.4 2.2 2.6 2.6.6.2.8-.6 1.4-.6.6 0 2.2.4 2.2 1 0 1-1 2.2-2 2.2C6.5 12.3 3.7 9.5 3.7 6 3.7 4.6 4.4 3.5 5 3.5z" fill="#fff"/></svg>
          <span>480-555-0187</span>
        </li>
        <li class="contact__item">
          <svg class="contact__icon" viewBox="0 0 16 16"><rect width="16" height="16" rx="2" fill="#111"/><circle cx="8" cy="8" r="4.6" fill="none" stroke="#fff" stroke-width="1.3"/><path d="M3.4 8h9.2M8 3.4c-2 2.6-2 6.6 0 9.2M8 3.4c2 2.6 2 6.6 0 9.2" fill="none" stroke="#fff" stroke-width="1"/></svg>
          <span>www.tallpinecomputing.com</span>
        </li>
        <li class="contact__item">
          <svg class="contact__icon" viewBox="0 0 16 16"><rect width="16" height="16" rx="2" fill="#111"/><path d="M3.5 8.2 8 4l4.5 4.2h-1.3V12H9.2V9.5H6.8V12H4.8V8.2z" fill="#fff"/></svg>
          <span>1200 N. Ridgeview Road Mesa,<br>Arizona 85201</span>
        </li>
      </ul>
    </div>

    <div class="band">
      <div class="band__stripe"></div>
      <div class="band__body">Also maybe our tagline which is "rooted in technology"</div>
      <div class="band__stripe band__stripe--bottom"></div>
    </div>
  </section>

  <section class="card card--back" aria-label="Business card back">
    <div class="back__mascot" role="img" aria-label="Cartoon fish mascot illustration in blue outline on black"></div>
    <div class="brand back__brand"><span class="brand__mark"></span><span>Tall Pine Computing</span></div>
  </section>

</body>
</html>
```